New Business Card Design Project LORVANTI-Italy

we are LORVANTI-Italy
our company in the market for 3 years we are luxury cosmetic company and its about time for a facelift :)
i will like to have elegant luxurious and unique business card
that will give the person that get it a unique, luxurious and elegant impression
I'm VERY OPEN FOR NEW IDEAS , even duo i add a few files of things that i see on line and i like them

i add my logo as well
my website is LORVANTI.COM
(if you would like to see the main style that we have)

Target Market(s)

adult that have money :)

Industry/Entity Type

Business

Contact Information for Business Card

Name - Dario Lorvanti
Position - CEO and CO Founder
address - 4817 E Halvern
telephone - 555-384-1926
email - dario@lorvanti.com
fax - 555-384-1926
website - LORVANTI.COM

Colors
000000
959595
fbee3e
ffffff

Requirements
Must have
• big logo in GOLD color
• elegant look
• impressive
Nice to have
• not must but maybe classy pattern background
• not must but maybe emblem
• maybe clear plastic business card
Should not have
• colors
• images

```html
<!DOCTYPE html>
<html lang="en">
<head>
<meta charset="utf-8">
<title>LORVANTI Italy — Business Card</title>
<link rel="stylesheet" href="https://fonts.googleapis.com/css2?family=Open+Sans:wght@400;600;700&display=swap">
<style>
  :root {
    --backdrop: #3a302b;
    --card: #111111;
    --card-edge: #1c1c1c;
    --gold: #d9a635;
    --gold-soft: #b8892a;
    --white: #ffffff;
    --grey: #959595;
  }
  * { box-sizing: border-box; margin: 0; padding: 0; }
  html, body {
    width: 1200px; height: 864px; overflow: hidden;
    background: var(--backdrop);
    font-family: "Open Sans", Arial, sans-serif;
  }
  .canvas { position: relative; width: 1200px; height: 864px; }

  .card {
    position: absolute;
    width: 520px; height: 297px;
    background: var(--card);
    border: 1px solid var(--card-edge);
    box-shadow: 0 14px 30px rgba(0,0,0,0.45);
  }

  /* front */
  .card-front { left: 70px; top: 100px; }
  .card-front .brand {
    position: absolute; left: 0; right: 0; top: 54px;
    display: flex; flex-direction: column; align-items: center;
  }
  .brand-dot {
    width: 74px; height: 74px; border-radius: 50%;
    border: 3px solid var(--gold);
  }
  .brand-name {
    margin-top: 14px;
    color: var(--gold); font-weight: 600;
    font-size: 34px; letter-spacing: 2px; line-height: 1;
  }
  .brand-sub {
    margin-top: 6px; padding-top: 6px;
    border-top: 2px solid var(--gold);
    color: var(--gold); font-weight: 600;
    font-size: 12px; letter-spacing: 3px;
    width: 200px; text-align: center;
  }
  .card-front .site {
    position: absolute; left: 0; right: 0; bottom: 36px;
    text-align: center; color: var(--grey);
    font-size: 13px; letter-spacing: 4px;
  }

  /* back */
  .card-back { left: 610px; top: 430px; }
  .contact { position: absolute; left: 30px; top: 128px; color: var(--white); }
  .contact-name { color: var(--gold); font-weight: 700; font-size: 17px; }
  .contact-role { font-size: 13px; margin-top: 2px; }
  .contact-lines { margin-top: 14px; font-size: 11px; line-height: 1.7; }
  .contact-lines .label { color: var(--gold); font-weight: 700; }
  .card-back .brand {
    position: absolute; right: 30px; top: 40px;
    display: flex; flex-direction: column; align-items: center;
  }
  .card-back .brand-dot { width: 60px; height: 60px; }
  .card-back .brand-name { font-size: 27px; margin-top: 12px; }
  .card-back .brand-sub { width: 170px; font-size: 10px; }
  .rule { position: absolute; left: 30px; right: 30px; height: 1px; background: var(--gold-soft); }
  .rule-top { top: 182px; left: 30px; right: 200px; }
  .rule-bottom { bottom: 30px; }
</style>
</head>
<body>
<main class="canvas">
  <section class="card card-front">
    <div class="brand">
      <span class="brand-dot"></span>
      <span class="brand-name">LORVANTI</span>
      <span class="brand-sub">ITALY</span>
    </div>
    <p class="site">www.lorvanti.com</p>
  </section>

  <section class="card card-back">
    <div class="brand">
      <span class="brand-dot"></span>
      <span class="brand-name">LORVANTI</span>
      <span class="brand-sub">ITALY</span>
    </div>
    <div class="contact">
      <p class="contact-name">Dario Lorvanti</p>
      <p class="contact-role">CEO &amp; CO Founder</p>
      <p class="contact-lines">
        4817 E Halvern | <span class="label">P :</span> 555-384-1926 <span class="label">F :</span> 555-384-1926<br>
        <span class="label">E :</span> dario@lorvanti.com <span class="label">W :</span> LORVANTI.COM
      </p>
    </div>
    <span class="rule rule-top"></span>
    <span class="rule rule-bottom"></span>
  </section>
</main>
</body>
</html>
```